Meridale Bed Company Needs Business Card

Looking for a very nice looking business card. Creative but not extravagant. We sell beds and pillows across the U.S. and need something professional but catchy. I have attached the logo.

Name : Devin Holt
Title : President
Phone : (800) 471-2960
Email: sleep@quilmora.com
Website: www.quilmora.com

Can be single-sided or double-sided
horizontal or vertical

Can use Blues/Greys

Target Market(s)

Mass Market

Industry/Entity Type

Retail

Contact Information for Business Card

Name : Devin Holt
Title : President
Phone : (800) 471-2960
Email: sleep@quilmora.com
Website: www.quilmora.com

Requirements
Must have
• Clean, Modern, Smooth
• Can use Blues/Greys
• On the other side without the information - have something simple like www.quilmora.com or our logo
Nice to have
• Surprise me
Should not have
• Nothing crazy, nothing cluttered

```html
<!DOCTYPE html>
<html lang="en">
<head>
<meta charset="utf-8">
<title>Meridale Bed Company – Business Card</title>
<link rel="stylesheet" href="https://fonts.googleapis.com/css2?family=Arimo:wght@400;700&display=swap">
<style>
  :root {
    --stage: #2e2926;
    --card-blue: #4c8bab;
    --wordmark-blue-soft: #74b6d2;
    --card-grey: #575757;
    --accent-blue: #38a9e0;
    --text-white: #f2f2f2;
    --divider: #cfcfcf;
  }
  * { margin: 0; padding: 0; box-sizing: border-box; }
  html, body {
    width: 1200px; height: 769px; overflow: hidden;
    background: var(--stage);
    font-family: "Arimo", Arial, sans-serif;
  }
  .stage {
    position: relative; width: 1200px; height: 769px;
    display: flex; align-items: center; justify-content: center; gap: 60px;
  }
  .card {
    position: relative; width: 520px; height: 297px;
    box-shadow: 0 10px 30px rgba(0,0,0,.45);
  }
  .card--front { background: var(--card-blue); }
  .card--back { background: var(--card-grey); }

  .brand-name {
    font-family: "Arimo", Arial, sans-serif;
    font-weight: 400;
    line-height: 1;
    position: absolute;
  }
  .card--front .brand-name {
    color: var(--wordmark-blue-soft);
    font-size: 62px;
    left: 0; right: 0; top: 114px; text-align: center;
  }
  .card--back .brand-name {
    color: var(--accent-blue);
    font-size: 62px;
    left: 190px; top: 78px;
  }

  .holder {
    position: absolute; right: 312px; top: 182px; text-align: right;
  }
  .holder__name { color: var(--accent-blue); font-weight: 700; font-size: 17px; }
  .holder__title { color: var(--text-white); font-weight: 400; font-size: 16px; margin-top: 3px; }

  .divider {
    position: absolute; left: 222px; top: 176px; width: 1.5px; height: 70px;
    background: var(--divider);
  }

  .contact {
    position: absolute; left: 236px; top: 184px; list-style: none;
    color: var(--text-white); font-size: 14px; font-weight: 400;
  }
  .contact__item { display: flex; align-items: center; gap: 8px; height: 20px; }
  .contact__icon { width: 13px; height: 13px; fill: var(--accent-blue); flex: none; }
</style>
</head>
<body>
<main class="stage">
  <section class="card card--front" aria-label="Card front">
    <div class="brand-name">quilmora</div>
  </section>

  <section class="card card--back" aria-label="Card back">
    <div class="brand-name">quilmora</div>

    <div class="holder">
      <div class="holder__name">Devin Holt</div>
      <div class="holder__title">President</div>
    </div>

    <div class="divider"></div>

    <ul class="contact">
      <li class="contact__item">
        <svg class="contact__icon" viewBox="0 0 16 16" aria-hidden="true"><path d="M3 1h3l1.5 4-2 1.3a9 9 0 0 0 4.2 4.2L11 8.5l4 1.5v3a2 2 0 0 1-2 2A12 12 0 0 1 1 3a2 2 0 0 1 2-2z"/></svg>
        (800) 471-2960
      </li>
      <li class="contact__item">
        <svg class="contact__icon" viewBox="0 0 16 16" aria-hidden="true"><path d="M1 3h14v10H1z M1.5 3.5 8 9l6.5-5.5" fill="none" stroke="#38a9e0" stroke-width="1.6"/><path d="M1 3h14L8 8.5z"/></svg>
        sleep@quilmora.com
      </li>
      <li class="contact__item">
        <svg class="contact__icon" viewBox="0 0 16 16" aria-hidden="true"><circle cx="8" cy="8" r="7"/><path d="M1 8h14M8 1c-2.5 2-2.5 12 0 14M8 1c2.5 2 2.5 12 0 14" fill="none" stroke="#575757" stroke-width="1.1"/></svg>
        www.quilmora.com
      </li>
    </ul>
  </section>
</main>
</body>
</html>
```